Website for Excavator and Earthworks Company

We require a modern, sleek and practical website for our newly created earthworks/excavator business in Perth, Western Australia called Bluegum Ridge Earthworks.

The website should have a modern, cutting edge feel but only needs to be relatively simplistic in it's layout and eventual functionality.

Some pages it should have would be Home, About, Projects and Contact Us.

```html
<!DOCTYPE html>
<html lang="en">
<head>
<meta charset="utf-8">
<title>Bluegum Ridge Earthworks</title>
<link rel="stylesheet" href="https://fonts.googleapis.com/css2?family=Michroma&family=Nunito+Sans:wght@400;600;700;800&display=swap">
<style>
:root{
  --lime:#c6d800;
  --black:#000;
  --ink:#1a1a1a;
  --white:#fff;
  --dark:#23292b;
  --muted:#333;
}
*{box-sizing:border-box;margin:0;padding:0}
html,body{width:1200px;height:4098px;overflow:hidden}
body{position:relative;background:var(--white);font-family:"Nunito Sans",sans-serif;color:var(--ink)}
.abs{position:absolute}
.display{font-family:"Michroma",sans-serif;color:var(--lime);font-size:29px;letter-spacing:1px;text-transform:uppercase;line-height:1;white-space:nowrap}
.kicker{font-size:21px;font-weight:600;color:var(--ink)}
.copy{font-size:14px;line-height:24px;color:var(--muted)}
.btn{position:absolute;display:flex;align-items:center;justify-content:center;font-weight:700;font-size:15px;text-decoration:none}
.btn--lime{background:var(--lime);color:var(--black)}
.btn--black{background:var(--black);color:var(--white)}
.photo{position:absolute}

/* hero */
.hero{position:absolute;left:0;top:0;width:1200px;height:760px;background:radial-gradient(ellipse at 70% 30%,#8a7a52 0%,#5a5446 30%,#3b3a36 60%,#262522 100%)}
.hero__shape{position:absolute;left:0;top:0}
.brand{position:absolute;left:154px;top:22px;width:210px;color:var(--white);font-family:"Nunito Sans",sans-serif;font-weight:800;text-align:center;text-transform:uppercase}
.brand__name{font-size:22px;letter-spacing:1px;line-height:1.1}
.brand__sub{font-size:11px;letter-spacing:4px;margin-top:4px}
.brand__mark{width:40px;height:40px;background:var(--lime);margin:0 auto 10px}
.phone{position:absolute;left:886px;top:8px;display:flex;align-items:center;gap:12px;color:var(--white);font-size:16px;font-weight:600}
.phone__icon{width:34px;height:34px;border-radius:50%;background:var(--lime);display:flex;align-items:center;justify-content:center}
.nav{position:absolute;top:68px;left:700px;display:flex;gap:34px;color:var(--white);font-size:14px;font-weight:700}
.nav__item{position:relative;padding:0 4px}
.nav__item--active::after{content:"";position:absolute;left:-10px;right:-10px;top:36px;height:4px;background:var(--lime)}
.hero__title{position:absolute;left:0;width:1200px;top:302px;text-align:center;font-family:"Michroma",sans-serif;color:var(--white);font-size:34px;line-height:45px;letter-spacing:1px;text-transform:uppercase}
.hero__arrows{position:absolute;top:580px;left:570px;display:flex;gap:18px}

/* welcome */
.frame{position:absolute;border:2px solid var(--lime)}
.badge{position:absolute;left:585px;top:1066px;width:160px;height:160px}

.feature{position:absolute;top:1278px;width:215px;height:127px;background:var(--black);color:var(--white);display:flex;flex-direction:column;align-items:center;justify-content:center;gap:12px;font-weight:700;font-size:15px}
.feature--lime{background:var(--lime);color:var(--white)}
.feature__stat{font-size:32px;font-weight:700;line-height:1}

.project__title{position:absolute;font-size:25px;font-weight:700;color:var(--ink)}
.project__copy{position:absolute;width:270px}

/* testimonials */
.testimonials{position:absolute;left:0;top:2597px;width:1200px;height:518px;background:radial-gradient(ellipse at 65% 35%,#4f5a5c 0%,#323a3c 45%,#1e2325 100%)}
.avatar{position:absolute;left:188px;top:2798px;width:134px;height:134px;border-radius:50%;background:linear-gradient(160deg,#b59276,#6d5a4e);border:5px solid #1b2022;box-shadow:0 0 0 2px #445}
.quote{position:absolute;font-family:Georgia,serif;font-weight:700;font-size:60px;color:var(--lime);line-height:1}

/* newsletter */
.newsletter{position:absolute;left:0;top:3115px;width:1200px;height:137px;background:var(--lime)}
.field{position:absolute;border:1.5px solid #333;background:var(--white);font-size:14px;color:#333;padding:0 20px;display:flex;align-items:center}

/* footer */
.footer{position:absolute;left:0;top:3823px;width:1200px;height:275px;background:var(--black);color:var(--white)}
.footer__head{position:absolute;top:62px;color:var(--lime);font-size:20px;font-weight:700}
.footer__list{position:absolute;top:95px;font-size:14px;line-height:24px;list-style:none}
.social{position:absolute;top:102px;width:42px;height:42px;border-radius:50%;background:var(--lime)}
</style>
</head>
<body>

<header class="hero">
  <div class="abs" role="img" aria-label="Yellow excavator digging and throwing soil under a cloudy sky" style="inset:0"></div>
  <svg class="hero__shape" width="1200" height="760" viewBox="0 0 1200 760" aria-hidden="true">
    <polygon points="0,612 660,688 0,735" fill="#c6d800"/>
    <polygon points="0,735 660,688 1200,690 1200,760 0,760" fill="#000"/>
    <polygon points="0,752 650,684 1200,700 1200,760 0,760" fill="#fff"/>
  </svg>
  <div class="brand">
    <div class="brand__mark"></div>
    <div class="brand__name">Bluegum Ridge</div>
    <div class="brand__sub">Earthworks</div>
  </div>
  <div class="phone">
    <span class="phone__icon"><svg width="16" height="16" viewBox="0 0 24 24"><path fill="#fff" d="M6.6 10.8a15 15 0 0 0 6.6 6.6l2.2-2.2c.3-.3.7-.4 1-.2 1.1.4 2.3.6 3.6.6.6 0 1 .4 1 1V20c0 .6-.4 1-1 1A17 17 0 0 1 3 4c0-.6.4-1 1-1h3.5c.6 0 1 .4 1 1 0 1.3.2 2.5.6 3.6.1.3 0 .7-.2 1z"/></svg></span>
    1-800 555 0147
  </div>
  <nav class="nav">
    <span class="nav__item nav__item--active">Home</span>
    <span class="nav__item">About Us</span>
    <span class="nav__item">Projects</span>
    <span class="nav__item">Contact Us</span>
  </nav>
  <h1 class="hero__title">We provide best construction<br>equipment for you</h1>
  <a class="btn btn--lime" style="left:528px;top:417px;width:144px;height:41px;font-weight:600">Get in Touch</a>
  <div class="hero__arrows">
    <svg width="16" height="24" viewBox="0 0 16 24"><path d="M11 4 4 12l7 8" stroke="#fff" stroke-width="2.5" fill="none"/></svg>
    <svg width="16" height="24" viewBox="0 0 16 24"><path d="M5 4l7 8-7 8" stroke="#fff" stroke-width="2.5" fill="none"/></svg>
  </div>
</header>

<section class="welcome">
  <p class="kicker abs" style="left:140px;top:808px">Welcome</p>
  <h2 class="display abs" style="left:138px;top:842px">Bluegum Ridge</h2>
  <p class="copy abs" style="left:137px;top:888px;width:430px">Lorem ipsum dolor sit amet, consectetur adipiscing elit, sed do eiusmod tempor incididunt ut labore et dolore magna aliqua. Quis ipsum suspendisse ultrices gravida. Risus commodo viverra maecenas accumsan lacus vel facilisis.<br>Lorem ipsum dolor sit amet, consectetur adipiscing elit, sed do eiusmod tempor incididunt ut labore et dolore magna aliqua. Quis ipsum suspendisse ultrices gravida. Risus commodo viverra maecenas accumsan lacus vel facilisis.</p>
  <a class="btn btn--lime" style="left:137px;top:1103px;width:143px;height:40px">Read More</a>
  <div class="frame" style="left:595px;top:769px;width:455px;height:393px"></div>
  <div class="photo" role="img" aria-label="Excavator bucket scooping earth at sunset" style="left:610px;top:781px;width:453px;height:395px;background:linear-gradient(150deg,#8a5a2a 0%,#c7852f 30%,#6d4a2c 60%,#3a2a1d 100%)"></div>
  <svg class="badge" viewBox="0 0 160 160" aria-label="15 years">
    <circle cx="80" cy="80" r="79" fill="#000"/>
    <circle cx="80" cy="80" r="72" fill="none" stroke="#fff" stroke-width="1.5"/>
    <defs><path id="ring" d="M80,80 m-58,0 a58,58 0 1,1 116,0 a58,58 0 1,1 -116,0"/></defs>
    <text font-family="Nunito Sans,sans-serif" font-size="9.5" font-weight="700" fill="#fff" letter-spacing="1"><textPath href="#ring">Bluegum Ridge Earthworks · Bluegum Ridge Earthworks ·</textPath></text>
    <text x="80" y="88" text-anchor="middle" font-family="Nunito Sans,sans-serif" font-size="48" font-weight="600" fill="#fff">15</text>
    <text x="80" y="115" text-anchor="middle" font-family="Nunito Sans,sans-serif" font-size="22" font-weight="600" fill="#fff">Year</text>
  </svg>
</section>

<section class="features">
  <div class="feature" style="left:137px">
    <svg width="38" height="38" viewBox="0 0 24 24"><rect x="3" y="5" width="18" height="16" rx="2" fill="#fff"/><rect x="6" y="2" width="2.5" height="5" rx="1" fill="#fff"/><rect x="15.5" y="2" width="2.5" height="5" rx="1" fill="#fff"/><rect x="3" y="9" width="18" height="1.5" fill="#000"/></svg>
    Same-Day Service
  </div>
  <div class="feature feature--lime" style="left:371px;width:213px">
    <span class="feature__stat">100%</span>
    Satisfaction Rating
  </div>
  <div class="feature" style="left:605px">
    <svg width="42" height="42" viewBox="0 0 24 24"><path fill="#fff" d="M12 1l2.2 2.6 3.3-.8.6 3.3 3.1 1.4-1.4 3.1 1.4 3.1-3.1 1.4-.6 3.3-3.3-.8L12 23l-2.2-2.6-3.3.8-.6-3.3-3.1-1.4 1.4-3.1-1.4-3.1 3.1-1.4.6-3.3 3.3.8z"/></svg>
    Best Price Guarantee
  </div>
  <div class="feature" style="left:840px">
    <svg width="40" height="42" viewBox="0 0 24 26"><circle cx="12" cy="9" r="8" fill="#fff"/><circle cx="12" cy="9" r="4" fill="#000"/><path d="M6 15l-2 9 4-2 3 3 1-8zM18 15l2 9-4-2-3 3-1-8z" fill="#fff"/></svg>
    Certifications
  </div>
</section>

<section class="projects">
  <p class="kicker abs" style="left:142px;top:1486px">What we do</p>
  <h2 class="display abs" style="left:140px;top:1520px">Projects</h2>

  <div class="photo" role="img" aria-label="Excavator landscaping a garden beside a house" style="left:137px;top:1585px;width:291px;height:236px;background:linear-gradient(170deg,#a9c6e0 0%,#c9b98a 35%,#5b7a3a 60%,#5a3e28 100%)"></div>
  <h3 class="project__title" style="left:148px;top:1830px">Landscaping</h3>
  <p class="copy project__copy" style="left:148px;top:1864px">Lorem ipsum dolor sit amet, consectetur adipiscing elit, sed do eiusmod tempor incididunt ut labore et dolore.</p>
  <a class="btn btn--black" style="left:148px;top:1950px;width:142px;height:41px">Read More</a>

  <div class="frame" style="left:460px;top:1576px;width:290px;height:235px"></div>
  <div class="photo" role="img" aria-label="Two workers in safety vests at a construction site with excavators" style="left:450px;top:1585px;width:290px;height:236px;background:linear-gradient(170deg,#c8d4dc 0%,#b8a486 45%,#7a6248 75%,#5a4636 100%)"></div>
  <h3 class="project__title" style="left:465px;top:1830px">Construction</h3>
  <p class="copy project__copy" style="left:466px;top:1864px">Lorem ipsum dolor sit amet, consectetur adipiscing elit, sed do eiusmod tempor incididunt ut labore et dolore.</p>
  <a class="btn btn--lime" style="left:463px;top:1950px;width:143px;height:41px">Read More</a>

  <div class="photo" role="img" aria-label="Excavator bucket moving soil" style="left:770px;top:1585px;width:292px;height:236px;background:linear-gradient(170deg,#9fb8d4 0%,#d9c28a 35%,#9a6a3e 65%,#6a4630 100%)"></div>
  <h3 class="project__title" style="left:782px;top:1830px">Replacement</h3>
  <p class="copy project__copy" style="left:783px;top:1864px">Lorem ipsum dolor sit amet, consectetur adipiscing elit, sed do eiusmod tempor incididunt ut labore et dolore.</p>
  <a class="btn btn--black" style="left:782px;top:1950px;width:143px;height:41px">Read More</a>
</section>

<section class="why">
  <p class="kicker abs" style="left:137px;top:2133px">Bluegum Ridge</p>
  <h2 class="display abs" style="left:136px;top:2167px">Why choose us</h2>
  <p class="copy abs" style="left:137px;top:2216px;width:430px">Lorem ipsum dolor sit amet, consectetur adipiscing elit, sed do eiusmod tempor incididunt ut labore et dolore magna aliqua. Quis ipsum suspendisse ultrices gravida. Risus commodo viverra maecenas accumsan lacus vel facilisis.<br>Lorem ipsum dolor sit amet, consectetur adipiscing elit, sed do eiusmod tempor incididunt ut labore et dolore magna aliqua. Quis ipsum suspendisse ultrices gravida. Risus commodo viverra maecenas accumsan lacus vel facilisis.</p>
  <a class="btn btn--lime" style="left:136px;top:2427px;width:143px;height:41px">Read More</a>
  <div class="frame" style="left:597px;top:2102px;width:453px;height:393px"></div>
  <div class="photo" role="img" aria-label="Three engineers in hard hats discussing in front of shipping containers" style="left:610px;top:2115px;width:453px;height:395px;background:linear-gradient(110deg,#2f4f86 0%,#44679e 40%,#8a8f98 65%,#c2b9a8 100%)"></div>
</section>

<section class="testimonials" role="img" aria-label="Dim excavator silhouette behind customer testimonial">
  <p class="abs" style="left:142px;top:58px;font-size:21px;font-weight:600;color:#fff">What Customer Says</p>
  <h2 class="display abs" style="left:140px;top:92px">Testimonials</h2>
  <svg class="abs" style="left:132px;top:258px" width="18" height="26" viewBox="0 0 18 26"><path d="M13 3 4 13l9 10" stroke="#fff" stroke-width="2.5" fill="none"/></svg>
  <svg class="abs" style="left:1040px;top:258px" width="18" height="26" viewBox="0 0 18 26"><path d="M5 3l9 10-9 10" stroke="#fff" stroke-width="2.5" fill="none"/></svg>
</section>
<div class="avatar" role="img" aria-label="Portrait of a smiling customer"></div>
<span class="quote" style="left:356px;top:2760px">&ldquo;</span>
<p class="abs" style="left:355px;top:2815px;width:665px;font-size:14px;line-height:24px;color:#fff">Lorem ipsum dolor sit amet, consectetur adipiscing elit, sed do eiusmod tempor incididunt ut labore et dolore magna aliqua. Quis ipsum suspendisse ultrices gravida. Risus commodo viverra maecenas accumsan lacus vel facilisis. Lorem ipsum dolor sit amet, consectetur adipiscing elit, sed do eiusmod tempor incididunt ut labore et dolore magna aliqua. Quis ipsum suspendisse ultrices gravida. Risus commodo viverra maecenas accumsan lacus vel facilisis.</p>
<span class="quote" style="left:736px;top:2916px">&rdquo;</span>

<section class="newsletter">
  <p class="abs" style="left:139px;top:30px;font-size:21px;font-weight:600;color:#fff">Join Our</p>
  <h2 class="display abs" style="left:138px;top:66px;color:#fff">Newsletter</h2>
  <div class="field" style="left:479px;top:54px;width:428px;height:43px;border:none">Enter Email Id</div>
  <a class="btn btn--black" style="left:920px;top:54px;width:142px;height:43px">Subscribe</a>
</section>

<section class="quote-request">
  <svg class="abs" style="left:0;top:3252px" width="1200" height="571" aria-hidden="true"><polygon points="649,0 1200,0 1200,571 603,571" fill="#6c5a42"/></svg>
  <div class="photo" role="img" aria-label="Smiling worker in a hard hat and orange jacket with arms crossed" style="left:603px;top:3252px;width:597px;height:571px;clip-path:polygon(46px 0,597px 0,597px 571px,0 571px);background:linear-gradient(120deg,#5d6a6e 0%,#c98a3a 45%,#d66b1e 60%,#3c4044 100%)"></div>
  <p class="kicker abs" style="left:143px;top:3290px">Get in Touch</p>
  <h2 class="display abs" style="left:141px;top:3324px">Request quote</h2>
  <div class="field" style="left:140px;top:3385px;width:406px;height:49px">Name</div>
  <div class="field" style="left:140px;top:3454px;width:406px;height:49px">Email</div>
  <div class="field" style="left:140px;top:3522px;width:406px;height:49px">Phone</div>
  <div class="field" style="left:140px;top:3594px;width:406px;height:113px;align-items:flex-start;padding-top:20px">Message</div>
  <a class="btn btn--lime" style="left:140px;top:3718px;width:143px;height:43px">Submit</a>
</section>

<footer class="footer">
  <div class="brand" style="left:146px;top:55px;width:212px">
    <div class="brand__mark"></div>
    <div class="brand__name">Bluegum Ridge</div>
    <div class="brand__sub">Earthworks</div>
  </div>
  <h4 class="footer__head" style="left:423px">Quick Links</h4>
  <ul class="footer__list" style="left:425px">
    <li>Home</li><li>About Us</li><li>Projects</li><li>Contact Us</li>
  </ul>
  <h4 class="footer__head" style="left:624px">Contact Us</h4>
  <ul class="footer__list" style="left:626px">
    <li>#123, Lorium ipsum,</li><li>Dolor amit,</li><li>Perth WA.</li><li>1800 555 0192</li><li>info@bluegumridge.example</li>
  </ul>
  <h4 class="footer__head" style="left:872px">Follow Us</h4>
  <span class="social" style="left:872px" role="img" aria-label="Social profile"></span>
  <span class="social" style="left:918px" role="img" aria-label="Social profile"></span>
  <span class="social" style="left:966px" role="img" aria-label="Social profile"></span>
  <span class="social" style="left:1013px" role="img" aria-label="Social profile"></span>
  <p class="abs" style="left:145px;top:192px;font-size:14px">&copy; 2026 | www.bluegumridge.example</p>
  <p class="abs" style="left:883px;top:194px;font-size:12px">Privacy Policy, Terms &amp; Conditions</p>
</footer>

</body>
</html>
```